Soho based IT support firm flyer.

We need a flyer to boost our business. We're a tech support firm based in Soho, London and provide helpdesk and call out support to SMEs in and around London.
They'll be two flyers with the same design. One is location specific and has the copy:
-
1 Month Free IT Support!
Based in Soho, we provide expert tech support for both laptops and desktops.
We have monthly as well as pay-as-you-go plans to fit your business.
Call us now and we'll show you how we can save you up to 50% on your IT spend.
-None location based is-
1 Month Free IT Support!
We provide expert, professional tech support for both laptops and desktops.
• Dedicated full time helpdesk
• Same day onsite visits
• Proactive support with monitoring
• 98% satisfaction score*
*taken from satisfaction survey sent out on closure of every case for Oct 2011 to Oct 2012
-
The location one needs to include a map with our location marked as postcode K7R 4TB.
I'm fine with royalty photos being used within a reasonable price. Please use Pixmarrow.
Our site shows our brand best. Please keep as close to this as possible.
http://quillnet-hub.example
Thanks for looking.

```html
<!DOCTYPE html>
<html lang="en">
<head>
<meta charset="utf-8">
<title>Quillnet – Friendly &amp; Reliable Tech Support</title>
<link rel="stylesheet" href="https://fonts.googleapis.com/css2?family=Roboto:wght@400;500;700;900&display=swap">
<style>
  :root {
    --lime: #9cc31c;
    --lime-light: #c4dc5a;
    --orange: #f7931e;
    --charcoal: #3b3c3e;
    --charcoal-dark: #2c2d2f;
    --ink: #3a3a3a;
    --paper: #ffffff;
    --mist: #eef2f0;
    --sky-top: #bcd3e4;
    --sky-bottom: #f4f7f9;
    --footnote: #d8d8d8;
  }
  * { box-sizing: border-box; margin: 0; padding: 0; }
  html, body { width: 849px; height: 1200px; overflow: hidden; background: var(--paper); }
  body { font-family: "Roboto", Arial, sans-serif; }

  .flyer { position: relative; width: 849px; height: 1200px; overflow: hidden; background: linear-gradient(180deg, var(--paper) 0%, var(--mist) 45%, var(--paper) 100%); }

  .hero-photo {
    position: absolute; top: 0; right: 0; width: 600px; height: 390px;
    background: radial-gradient(ellipse at 65% 40%, var(--sky-bottom) 0%, var(--sky-top) 70%, #9fb9cc 100%);
  }

  .backdrop { position: absolute; inset: 0; }

  .offer-badge {
    position: absolute; left: 100px; top: 175px; width: 230px; height: 230px;
    border-radius: 50%; background: var(--orange); border: 8px solid var(--paper);
    box-shadow: 0 4px 10px rgba(0,0,0,.25);
    color: var(--paper); text-align: center; transform: rotate(-12deg);
    display: flex; flex-direction: column; justify-content: center; align-items: center;
  }
  .offer-badge .free { font-weight: 900; font-size: 66px; line-height: 1; letter-spacing: 1px; }
  .offer-badge .term { font-weight: 700; font-size: 27px; line-height: 1.15; margin-top: 4px; }

  .headline {
    position: absolute; left: 105px; top: 420px; color: var(--ink);
    font-weight: 500; font-size: 58px; line-height: 1.12; letter-spacing: -0.5px;
  }

  .services {
    position: absolute; left: 55px; top: 575px; width: 794px; height: 507px;
    background: var(--charcoal);
    display: flex; gap: 30px; padding: 38px 36px 0 28px;
  }
  .service-list { list-style: none; }
  .service-list.main { width: 400px; }
  .service-list.extras { width: 330px; }
  .service-list li {
    position: relative; padding-left: 40px; color: var(--paper);
    font-weight: 700; font-size: 27px; line-height: 1.28; margin-bottom: 24px;
  }
  .service-list li::before {
    content: ""; position: absolute; left: 0; top: 6px; width: 18px; height: 18px;
    border: 3px solid var(--paper); border-radius: 50%;
  }
  .footnote { display: block; font-weight: 400; font-size: 18px; line-height: 1.3; margin-top: 4px; color: var(--footnote); }

  .brand {
    position: absolute; left: 36px; top: 1102px; display: flex; align-items: center; gap: 14px;
    color: var(--lime); font-weight: 700; font-size: 62px; letter-spacing: -1px;
  }
  .brand .mark { width: 28px; height: 28px; background: var(--lime); }

  .contact { position: absolute; left: 505px; top: 1092px; width: 330px; color: var(--paper); }
  .contact .phone { display: flex; align-items: center; gap: 8px; font-weight: 700; font-size: 40px; line-height: 1; margin-bottom: 10px; }
  .contact .line { display: flex; align-items: center; gap: 12px; font-size: 20px; font-weight: 500; line-height: 1.4; }
  .contact .line::before { content: ""; width: 14px; height: 14px; background: var(--paper); }
</style>
</head>
<body>
<div class="flyer">
  <div class="hero-photo" role="img" aria-label="Photo of a businessman in a suit reaching up to floating screens of business imagery against a pale blue sky"></div>

  <svg class="backdrop" width="849" height="1200" viewBox="0 0 849 1200" aria-hidden="true">
    <path d="M0 0 H330 C250 60 170 140 120 260 L0 330 Z" fill="var(--charcoal)"/>
    <path d="M0 330 C180 230 420 200 849 300 V390 C520 320 260 330 0 430 Z" fill="var(--lime)"/>
    <path d="M0 430 C260 330 520 320 849 390 V405 C520 345 260 355 0 450 Z" fill="var(--lime-light)"/>
    <rect x="0" y="575" width="55" height="507" fill="var(--lime)"/>
    <path d="M400 1200 C425 1130 465 1082 540 1082 H849 V1200 Z" fill="var(--charcoal)"/>
  </svg>

  <div class="offer-badge">
    <span class="free">FREE</span>
    <span class="term">One Month<br>IT Support!</span>
  </div>

  <h1 class="headline">Friendly &amp;<br>Reliable Tech Support</h1>

  <section class="services">
    <ul class="service-list main">
      <li>We provide expert, professional tech support for laptops and desktops.</li>
      <li>We have monthly as well as pay-as-you-go plans to fit your business.</li>
      <li>Call us now and we'll show you how we can save you up to 50% on your IT spend.</li>
    </ul>
    <ul class="service-list extras">
      <li>Dedicated full time helpdesk</li>
      <li>Same day onsite visits</li>
      <li>Proactive support with monitoring</li>
      <li>98% satisfaction score*
        <span class="footnote">taken from satisfaction survey sent out on closure of every case for Oct 2011 to Oct 2012</span>
      </li>
    </ul>
  </section>

  <div class="brand"><span>Quillnet</span><span class="mark"></span></div>

  <div class="contact">
    <div class="phone">
      <svg width="34" height="34" viewBox="0 0 24 24" aria-hidden="true"><path fill="var(--orange)" d="M6.6 10.8a15 15 0 0 0 6.6 6.6l2.2-2.2c.3-.3.7-.4 1-.2 1.1.4 2.3.6 3.6.6.6 0 1 .4 1 1V20c0 .6-.4 1-1 1A17 17 0 0 1 3 4c0-.6.4-1 1-1h3.5c.6 0 1 .4 1 1 0 1.3.2 2.5.6 3.6.1.3 0 .7-.2 1z"/></svg>
      <span>0203 555 0147</span>
    </div>
    <div class="line">info@quillnet-hub.example</div>
    <div class="line">www.quillnet-hub.example</div>
  </div>
</div>
</body>
</html>
```